Business Cards - Brightpath Horizon

need to design unique business card for my mortgage business. I need to design credit card style business card for my business or any unique idea that you might have

Target Market(s)

Home Loan customers

Industry/Entity Type

Mortgage Brokerage

Contact Information for Business Card

please design credit card style or very unique style business card

Colors

Designer to choose colors to be used in the design.

Requirements
Must have
• Name
• position
• Phone number
• fax number
• email address
• website address
• social media address
• All above fields will be provided once design in finalised

```html
<!DOCTYPE html>
<html lang="en">
<head>
<meta charset="utf-8">
<title>Brightpath Horizon – Business Card</title>
<link href="https://fonts.googleapis.com/css2?family=Roboto:ital,wght@0,400;0,500;0,700;1,400&display=swap" rel="stylesheet">
<style>
  :root {
    --backdrop: #2b2b2b;
    --paper: #f4f4f4;
    --brand-blue: #0a2fc4;
    --brand-orange: #ff8c12;
    --ink: #4a4a4a;
    --white: #ffffff;
  }
  * { margin: 0; padding: 0; box-sizing: border-box; }
  html, body { width: 1200px; height: 960px; overflow: hidden; }
  body {
    background: var(--backdrop);
    font-family: "Roboto", Arial, sans-serif;
    position: relative;
  }
  .card {
    position: absolute;
    width: 600px;
    height: 342px;
    overflow: hidden;
    box-shadow: 0 4px 10px rgba(0,0,0,0.5);
  }
  .card-front { left: 314px; top: 113px; background: var(--paper); }
  .card-back { left: 311px; top: 472px; height: 343px; background: var(--brand-orange); }

  .front-brand {
    position: absolute;
    right: 30px;
    top: 56px;
    display: flex;
    align-items: center;
    gap: 10px;
  }
  .brand-mark { width: 16px; height: 16px; background: var(--brand-orange); }
  .brand-name {
    font-weight: 500;
    color: var(--brand-blue);
    font-size: 34px;
    line-height: 1;
    text-align: right;
    letter-spacing: 0.5px;
  }
  .front-tagline {
    position: absolute;
    right: 28px;
    top: 144px;
    font-size: 14px;
    font-style: italic;
    color: var(--brand-orange);
  }

  .holder { position: absolute; left: 26px; top: 175px; }
  .holder-name { font-size: 20px; font-weight: 700; color: var(--brand-blue); line-height: 24px; }
  .holder-role { font-size: 15px; font-weight: 500; color: var(--brand-orange); line-height: 22px; }
  .divider {
    position: absolute; left: 26px; top: 223px; width: 544px; height: 1.5px;
    background: var(--brand-blue);
  }
  .contact-list { position: absolute; left: 26px; top: 230px; list-style: none; }
  .contact-list li {
    display: flex; align-items: center; gap: 8px;
    font-size: 14px; color: var(--ink); height: 19px;
  }
  .contact-list svg { width: 14px; height: 14px; fill: var(--brand-blue); }
  .address {
    position: absolute; right: 26px; top: 269px;
    text-align: right; font-size: 14px; color: var(--ink); line-height: 19px;
  }
  .edge-band { position: absolute; left: 0; bottom: 0; width: 600px; height: 12px; }

  .back-brand {
    position: absolute; left: 0; width: 600px; top: 128px;
    text-align: center; color: var(--white);
  }
  .back-brand .brand-name { color: var(--white); font-size: 46px; text-align: center; line-height: 1.05; }
  .back-tagline { margin-top: 12px; font-size: 16px; font-style: italic; color: var(--white); }
  .social-row {
    position: absolute; left: 69px; top: 290px; width: 462px; height: 30px;
    display: flex; align-items: center; gap: 4px;
  }
  .social-rule { flex: 1; height: 1px; }
  .social-rule.left { background: linear-gradient(to right, transparent, var(--white)); margin-right: 6px; }
  .social-rule.right { background: linear-gradient(to left, transparent, var(--white)); margin-left: 6px; }
  .social-dot { width: 29px; height: 29px; border-radius: 50%; background: var(--white); }
</style>
</head>
<body>

<section class="card card-front" aria-label="Business card front">
  <div class="front-brand">
    <span class="brand-mark"></span>
    <div class="brand-name">Brightpath<br>Horizon</div>
  </div>
  <div class="front-tagline">Smart move, perfect timing</div>

  <div class="holder">
    <div class="holder-name">DANIEL REEVE</div>
    <div class="holder-role">CEO/FOUNDER</div>
  </div>
  <div class="divider"></div>

  <ul class="contact-list">
    <li>
      <svg viewBox="0 0 24 24" aria-hidden="true"><path d="M6.6 10.8a15.1 15.1 0 0 0 6.6 6.6l2.2-2.2a1 1 0 0 1 1-.25 11.4 11.4 0 0 0 3.6.57 1 1 0 0 1 1 1V20a1 1 0 0 1-1 1A17 17 0 0 1 3 4a1 1 0 0 1 1-1h3.5a1 1 0 0 1 1 1c0 1.25.2 2.45.57 3.57a1 1 0 0 1-.25 1z"/></svg>
      555 214 7730
    </li>
    <li>
      <svg viewBox="0 0 24 24" aria-hidden="true"><path d="M6 2h12v5H6z M3 8h18a1 1 0 0 1 1 1v8h-4v5H6v-5H2V9a1 1 0 0 1 1-1z M8 15v5h8v-5z"/></svg>
      555 214 7731
    </li>
    <li>
      <svg viewBox="0 0 24 24" aria-hidden="true"><path d="M2 5h20v14H2z M4 7v.5l8 5 8-5V7z" fill-rule="evenodd"/></svg>
      hello@bphorizon.com
    </li>
    <li>
      <svg viewBox="0 0 24 24" aria-hidden="true"><circle cx="12" cy="12" r="10"/><path d="M2 12h20M12 2c3 3 3 17 0 20M12 2c-3 3-3 17 0 20" stroke="#f4f4f4" stroke-width="1.4" fill="none"/></svg>
      www.bphorizon.com
    </li>
  </ul>

  <div class="address">2140 Alder Bend Road<br>Larch Falls, Alaska 99704</div>

  <svg class="edge-band" viewBox="0 0 600 12" preserveAspectRatio="none" aria-hidden="true">
    <polygon points="0,0 352,0 348,12 0,12" fill="var(--brand-blue)"/>
    <polygon points="356,0 600,0 600,12 352,12" fill="var(--brand-orange)"/>
  </svg>
</section>

<section class="card card-back" aria-label="Business card back">
  <div class="back-brand">
    <div class="brand-name">Brightpath<br>Horizon</div>
    <div class="back-tagline">Smart move, perfect timing</div>
  </div>
  <div class="social-row" aria-label="Social media links">
    <span class="social-rule left"></span>
    <span class="social-dot"></span>
    <span class="social-dot"></span>
    <span class="social-dot"></span>
    <span class="social-dot"></span>
    <span class="social-rule right"></span>
  </div>
</section>

</body>
</html>
```